Condo Debts Collection Business needs a Web Design (Contest)

I need a site for a client, who works with condo debts collection, and ensure all revenues provided by condo fees will be always available to the building manager of condo on a specific date, regardless of defaults.I have the logo of the companies, and some requirements on layout (kind of slider, menu options, phone number on a noble position, etc).
Updates

Designs look the same

Target Market(s)

I have two targets for this design: - Condominium's building manager. This target is looking for a solution to overdue debts on it's condo. - Residents on condominiums. This target wants to live in a better place, where their neighbors pay their condominium fees on time.

Number of Pages Required

1 page

Requirements
Must have
• - Slider with title, some short text related, a nice image (I prefer happy and/or peaceful family, people doing business, happy friends, and so on).
• - I have a special attention to menu. I'm looking for one I can have a nice effect, more elegant, charming, kind of innovative.
• - Phone number on the top (or clearly visible).
• - Member log in area or icon on the top (or clearly visible).
• - News/articles area.
• - Modern fonts, with good quality, sans-serif on areas where reading is more intensive (prefer Google web-fonts).
• - Colors specified on attached files.
• - Header similar or inspired by the "FILE 3"
Nice to have
• - Clear background color, cause it's better to read larger texts (like articles). Dark backgrounds makes reading difficult.
• - A site with effects (like shadows, lines, gradients, lights) is usually pretty.
• - I pay attention on beautiful footers.
Should not have
• - Images with a lot of money (I don't sell richness, I sell tranquility, peace, harmony, safety).
• - Poor menu.
• - Lots of curves. My customer asked for straight lines.

```html
<!DOCTYPE html>
<html lang="en">
<head>
<meta charset="utf-8">
<title>Serenvia</title>
<link href="https://fonts.googleapis.com/css2?family=Open+Sans:wght@400;600;700;800&display=swap" rel="stylesheet">
<style>
:root{
  --blue:#1c4a86;
  --blue-deep:#143a6c;
  --orange:#e8892a;
  --ink:#111;
  --text:#555;
  --light:#f2f2f2;
  --white:#fff;
  --footer:#000;
}
*{box-sizing:border-box;margin:0;padding:0}
html,body{width:1200px;height:3082px;overflow:hidden}
body{font-family:"Open Sans",Arial,sans-serif;color:var(--ink);background:var(--white);position:relative}
.abs{position:absolute}

/* header */
.header{position:absolute;top:0;left:0;width:1200px;height:138px;background:var(--white)}
.brand{left:110px;top:30px;display:flex;align-items:center;gap:12px}
.brand-mark{width:40px;height:40px;background:var(--blue)}
.brand-name{font-size:28px;font-weight:800;color:var(--blue)}
.topbar{left:400px;top:0;width:800px;height:56px;background:var(--orange);clip-path:polygon(0 0,100% 0,100% 100%,30px 100%)}
.topbar-item{top:11px;display:flex;align-items:center;gap:12px;color:var(--white);font-weight:700;font-size:19px}
.icon-circle{width:34px;height:34px;border-radius:50%;border:2px solid var(--white);display:flex;align-items:center;justify-content:center}
.social{top:10px;display:flex;gap:10px}
.social span{width:34px;height:34px;border-radius:50%;border:2px solid var(--white);display:block}
.nav{top:84px;left:456px;display:flex;gap:32px;font-size:16px;color:#333}
.nav a{color:inherit;text-decoration:none;padding-bottom:6px}
.nav a.active{border-bottom:2px solid var(--blue);padding:0 8px 6px}
.login{left:930px;top:77px;width:156px;height:42px;background:var(--blue);color:var(--white);font-weight:700;font-size:16px;display:flex;align-items:center;justify-content:center}

/* hero */
.hero{position:absolute;top:138px;left:0;width:1200px;height:576px;background:linear-gradient(135deg,#6f8b5a 0%,#a3b38a 40%,#7d8f55 70%,#5d6e3c 100%)}
.hero-title{left:112px;top:210px;font-size:38px;font-weight:800;color:var(--white);letter-spacing:.5px}
.hero-text{left:112px;top:265px;width:520px;font-size:17px;font-weight:600;line-height:30px;color:var(--white)}
.hero-btn{left:112px;top:340px;width:188px;height:54px;border:3px solid var(--white);color:var(--white);font-weight:700;font-size:19px;display:flex;align-items:center;justify-content:center;gap:14px}
.dots{left:1134px;top:272px;display:flex;flex-direction:column;gap:12px;align-items:center}
.dots span{width:10px;height:10px;border-radius:50%;background:var(--white);display:block}
.dots span.on{width:20px;height:20px;border:3px solid var(--white);background:transparent;position:relative}
.dots span.on::after{content:"";position:absolute;left:3px;top:3px;width:8px;height:8px;border-radius:50%;background:var(--white)}
.wave{left:0;top:532px}

/* about */
.about-title{left:0;top:798px;width:1200px;text-align:center;font-size:42px;font-weight:700}
.about-text{left:190px;top:878px;width:820px;text-align:center;font-size:16px;line-height:34px;color:var(--text)}
.btn-blue{left:514px;top:1073px;width:200px;height:64px;background:var(--blue);color:var(--white);font-weight:700;font-size:20px;display:flex;align-items:center;justify-content:center}

/* services */
.services{position:absolute;top:1200px;left:0;width:1200px;height:780px;background:linear-gradient(180deg,rgba(28,74,134,.88),rgba(20,58,108,.92)),linear-gradient(120deg,#8a96a8,#5c6b82 50%,#9ba4b0)}
.svc-kicker{left:110px;top:130px;font-size:22px;color:var(--white)}
.svc-title{left:110px;top:170px;width:400px;font-size:33px;line-height:44px;font-weight:700;color:var(--white)}
.svc-text{left:110px;top:272px;width:390px;font-size:15px;line-height:27px;color:#e6ecf5}
.stats{left:110px;top:570px;display:flex;gap:70px;color:var(--white)}
.stat b{display:block;font-size:28px;font-weight:700}
.stat span{font-size:18px}
.card{width:262px;height:280px;background:var(--blue-deep);padding:40px 30px;color:var(--white)}
.card svg{display:block;margin-bottom:26px}
.card h3{font-size:22px;font-weight:700;margin-bottom:14px}
.card p{font-size:14px;line-height:26px;color:#dbe3ee}

/* news */
.news{position:absolute;top:1980px;left:0;width:1200px;height:732px;background:var(--light)}
.news-title{left:0;top:90px;width:1200px;text-align:center;font-size:42px;font-weight:700}
.post{width:303px;top:200px}
.post-img{height:188px}
.post-head{display:flex;gap:14px;align-items:flex-start;margin-top:24px}
.date{flex:0 0 50px;height:50px;border-radius:50%;background:var(--blue);color:var(--white);text-align:center;font-size:16px;font-weight:700;line-height:18px;padding-top:8px}
.date small{display:block;font-size:12px;font-weight:400}
.post-head h4{font-size:17px;font-weight:600;line-height:26px}
.post p{font-size:15px;line-height:27px;color:var(--text);margin-top:14px}
.btn-outline{margin-top:22px;width:148px;height:46px;border:2px solid #555;font-size:17px;font-weight:700;display:flex;align-items:center;justify-content:center;background:var(--white)}

/* footer */
.footer{position:absolute;top:2712px;left:0;width:1200px;height:370px;background:var(--footer);color:var(--white)}
.f-brand{left:114px;top:140px;display:flex;align-items:center;gap:12px}
.f-brand .brand-mark{background:var(--white)}
.f-brand .brand-name{color:var(--white)}
.f-head{font-size:22px;font-weight:600}
.f-links{list-style:none;font-size:14px;line-height:29px;margin-top:18px}
.f-contact{margin-top:20px;font-size:14px}
.f-row{display:flex;gap:14px;margin-bottom:18px;line-height:22px}
.f-social{display:flex;gap:10px;margin-top:20px}
.f-social span{width:40px;height:40px;border-radius:50%;border:2px solid var(--white);display:block}
.subscribe{margin-top:14px;width:240px;height:34px;border-radius:17px;background:var(--white);color:#777;font-size:12px;display:flex;align-items:center;justify-content:space-between;padding:0 4px 0 16px}
.subscribe i{width:28px;height:28px;border-radius:50%;background:var(--blue);display:flex;align-items:center;justify-content:center}
.f-rule{left:110px;top:296px;width:976px;height:1px;background:#333}
.f-bottom{top:322px;font-size:13px;color:#ddd}
</style>
</head>
<body>

<header class="header">
  <div class="abs brand"><span class="brand-mark"></span><span class="brand-name">SERENVIA</span></div>
  <div class="abs topbar"></div>
  <div class="abs topbar-item" style="left:460px">
    <span class="icon-circle"><svg width="16" height="12" viewBox="0 0 16 12" fill="none" stroke="#fff" stroke-width="1.6"><rect x="1" y="1" width="14" height="10"/><path d="M1 1l7 6 7-6"/></svg></span>
    info@serenvia.com
  </div>
  <div class="abs topbar-item" style="left:740px">
    <span class="icon-circle"><svg width="16" height="16" viewBox="0 0 24 24" fill="#fff"><path d="M6.6 10.8a15 15 0 0 0 6.6 6.6l2.2-2.2c.3-.3.7-.4 1-.2 1.1.4 2.3.6 3.6.6.6 0 1 .4 1 1V20c0 .6-.4 1-1 1A17 17 0 0 1 3 4c0-.6.4-1 1-1h3.5c.6 0 1 .4 1 1 0 1.3.2 2.5.6 3.6.1.3 0 .7-.2 1z"/></svg></span>
    (555) 014 2290
  </div>
  <div class="abs social" style="left:956px"><span></span><span></span><span></span></div>
  <nav class="abs nav">
    <a class="active">Home</a><a>About Us</a><a>Services</a><a>News</a><a>Contact Us</a>
  </nav>
  <div class="abs login">Member Login</div>
</header>

<section class="hero" role="img" aria-label="Photo of a happy family running together across a sunny park">
  <h1 class="abs hero-title">WELCOME TO SERENVIA</h1>
  <p class="abs hero-text">Lorem ipsum dolor sit amet, consectetur adipiscing elit, sed do eiusmod tempor incididunt ut labore et dolore</p>
  <div class="abs hero-btn">Let's Go
    <svg width="40" height="12" viewBox="0 0 40 12" fill="none" stroke="#fff" stroke-width="2"><path d="M0 6h37M32 1l5 5-5 5"/></svg>
  </div>
  <div class="abs dots"><span class="on"></span><span></span><span></span></div>
  <svg class="abs wave" width="1200" height="46" viewBox="0 0 1200 46"><path d="M0 46V44H440C520 44 540 10 600 10S680 44 760 44H1200V46Z" fill="#fff"/><circle cx="600" cy="28" r="9" fill="none" stroke="#333" stroke-width="1.5"/><path d="M596 26l4 4 4-4" fill="none" stroke="#333" stroke-width="1.5"/></svg>
</section>

<section>
  <h2 class="abs about-title">About Us</h2>
  <p class="abs about-text">Lorem ipsum dolor sit amet, consectetur adipiscing elit, sed do eiusmod tempor incididunt ut labore et dolore magna aliqua. Ut enim ad minim veniam, quis nostrud exercitation ullamco laboris nisi ut aliquip ex ea commodo consequat. Duis aute irure dolor in reprehenderit in voluptate velit esse cillum dolore eu fugiat nulla pariatur. Excepteur sint occaecat cupidatat non proident, sunt in culpa qui officia deserunt mollit anim id est laborum</p>
  <div class="abs btn-blue">Read More</div>
</section>

<section class="services" role="img" aria-label="Background photo of business people in a bright office under a blue tint">
  <p class="abs svc-kicker">What We Do</p>
  <h2 class="abs svc-title">Sed ut perspiciatis unde omnis iste natus</h2>
  <p class="abs svc-text">Lorem ipsum dolor sit amet, consectetur adipiscing elit, sed do eiusmod tempor incididunt ut labore et dolore magna aliqua. Ut enim ad minim veniam, quis nostrud exercitation ullamco laboris nisi ut aliquip ex ea commodo consequat. Duis aute irure dolor in reprehenderit in voluptate velit esse cillum dolore eu fugiat nulla pariatur. Excepteur sint occaecat cupidatat non proident, sunt in culpa qui officia deserunt mollit anim id est laborum</p>
  <div class="abs stats">
    <div class="stat"><b>1500</b><span>Clients</span></div>
    <div class="stat"><b>10</b><span>Awards</span></div>
    <div class="stat"><b>2356</b><span>Works</span></div>
  </div>
  <div class="abs card" style="left:528px;top:120px">
    <svg width="56" height="52" viewBox="0 0 56 52" fill="none" stroke="#fff" stroke-width="2"><rect x="4" y="6" width="24" height="34"/><path d="M10 14h12M10 20h12M10 26h8"/><rect x="30" y="18" width="22" height="30"/><path d="M35 26h12M35 33h4M43 33h4M35 40h4M43 40h4"/></svg>
    <h3>Lorem ipsum dolor</h3><p>Lorem ipsum dolor amet, consectetur adis elit aliquam quis erat vitae dolor.</p>
  </div>
  <div class="abs card" style="left:818px;top:120px">
    <svg width="56" height="52" viewBox="0 0 56 52" fill="none" stroke="#fff" stroke-width="2"><rect x="4" y="8" width="34" height="24"/><path d="M12 8V4h18v4"/><circle cx="34" cy="36" r="10"/><path d="M34 31v10M44 40l8 6"/></svg>
    <h3>Lorem ipsum dolor</h3><p>Lorem ipsum dolor amet, consectetur adis elit aliquam quis erat vitae dolor.</p>
  </div>
  <div class="abs card" style="left:528px;top:430px">
    <svg width="56" height="52" viewBox="0 0 56 52" fill="none" stroke="#fff" stroke-width="2"><circle cx="28" cy="18" r="12"/><path d="M28 12v12M4 44h14l8-6h10M4 36h10l8-4"/></svg>
    <h3>Lorem ipsum dolor</h3><p>Lorem ipsum dolor amet, consectetur adis elit aliquam quis erat vitae dolor.</p>
  </div>
  <div class="abs card" style="left:818px;top:430px">
    <svg width="56" height="52" viewBox="0 0 56 52" fill="none" stroke="#fff" stroke-width="2"><circle cx="28" cy="28" r="9"/><path d="M28 4v12M18 8v10M38 8v10M10 40h36M14 46h28"/></svg>
    <h3>Lorem ipsum dolor</h3><p>Lorem ipsum dolor amet, consectetur adis elit aliquam quis erat vitae dolor.</p>
  </div>
</section>

<section class="news">
  <h2 class="abs news-title">Our News</h2>
  <article class="abs post" style="left:110px">
    <div class="post-img" role="img" aria-label="Photo of a family sitting by a lake" style="background:linear-gradient(180deg,#b9c7cf,#7f9460)"></div>
    <div class="post-head"><div class="date">29<small>Feb</small></div><h4>At vero eos et accusamus et iusto odio dignissimos</h4></div>
    <p>Lorem ipsum dolor sit amet, consectetur adipiscing elit, sed do eiusmod tempor incididunt ut labore et dolore magna aliqua.</p>
    <div class="btn-outline">Read More</div>
  </article>
  <article class="abs post" style="left:443px">
    <div class="post-img" role="img" aria-label="Photo of colleagues in a business meeting" style="background:linear-gradient(135deg,#e7e2dc,#8b8f9c 60%,#4a4f5c)"></div>
    <div class="post-head"><div class="date">29<small>Feb</small></div><h4>At vero eos et accusamus et iusto odio dignissimos</h4></div>
    <p>Lorem ipsum dolor sit amet, consectetur adipiscing elit, sed do eiusmod tempor incididunt ut labore et dolore magna aliqua.</p>
    <div class="btn-outline">Read More</div>
  </article>
  <article class="abs post" style="left:780px">
    <div class="post-img" role="img" aria-label="Photo of cheerful friends outdoors at sunset" style="background:linear-gradient(135deg,#f3d3a0,#c9885a 50%,#6d7f9a)"></div>
    <div class="post-head"><div class="date">29<small>Feb</small></div><h4>At vero eos et accusamus et iusto odio dignissimos</h4></div>
    <p>Lorem ipsum dolor sit amet, consectetur adipiscing elit, sed do eiusmod tempor incididunt ut labore et dolore magna aliqua.</p>
    <div class="btn-outline">Read More</div>
  </article>
</section>

<footer class="footer">
  <div class="abs f-brand"><span class="brand-mark"></span><span class="brand-name">SERENVIA</span></div>
  <div class="abs" style="left:368px;top:56px">
    <h3 class="f-head">Quick Links</h3>
    <ul class="f-links"><li>Home</li><li>About Us</li><li>Services</li><li>News</li><li>Contact Us</li></ul>
  </div>
  <div class="abs" style="left:536px;top:56px;width:240px">
    <h3 class="f-head">Contact Us</h3>
    <div class="f-contact">
      <div class="f-row"><svg width="14" height="18" viewBox="0 0 14 18" fill="#fff"><path d="M7 0a7 7 0 0 0-7 7c0 5 7 11 7 11s7-6 7-11a7 7 0 0 0-7-7zm0 10a3 3 0 1 1 0-6 3 3 0 0 1 0 6z"/></svg><div><b style="font-size:17px">Serenvia</b><br>14 Harbour Lane, Northvale<br>NSW 2100</div></div>
      <div class="f-row"><svg width="16" height="16" viewBox="0 0 24 24" fill="none" stroke="#fff" stroke-width="1.8"><path d="M6.6 10.8a15 15 0 0 0 6.6 6.6l2.2-2.2c.3-.3.7-.4 1-.2 1.1.4 2.3.6 3.6.6.6 0 1 .4 1 1V20c0 .6-.4 1-1 1A17 17 0 0 1 3 4c0-.6.4-1 1-1h3.5c.6 0 1 .4 1 1 0 1.3.2 2.5.6 3.6.1.3 0 .7-.2 1z"/></svg>(555) 014 2290</div>
      <div class="f-row"><svg width="18" height="14" viewBox="0 0 16 12" fill="none" stroke="#fff" stroke-width="1.4"><rect x="1" y="1" width="14" height="10"/><path d="M1 1l7 6 7-6"/></svg>info@serenvia.com</div>
    </div>
  </div>
  <div class="abs" style="left:837px;top:56px">
    <h3 class="f-head">Stay Connected</h3>
    <div class="f-social"><span></span><span></span><span></span></div>
    <h3 class="f-head" style="margin-top:18px">Subscribe To Newsletter</h3>
    <div class="subscribe">Enter Your Email<i><svg width="14" height="14" viewBox="0 0 14 14" fill="#fff"><path d="M1 6l12-5-5 12-1.5-5z"/></svg></i></div>
  </div>
  <div class="abs f-rule"></div>
  <p class="abs f-bottom" style="left:110px">© Copyrights 2019 | All Rights Reserved</p>
  <p class="abs f-bottom" style="left:798px">Terms &amp; Conditions of Use &nbsp;&nbsp;&nbsp;&nbsp;&nbsp; Privacy Policy</p>
</footer>

</body>
</html>
```